A Modern & Sleek "Coming Soon" Page for an A.I Recruiting App

For the “Coming Soon” website, a simple background with no people in it. I've attached an A.I image of what the page should generally look like.

- A single mobile phone as the main focus where the user actually clicks on the, “notify me” button (after entering their email address).
- In the background where the pillars/columns are seen in the example, should be subtle pad locks that are in their opened position with a key inside the lock. I've attached images to try to illustrate this idea, but they are far away in style from what I'm looking for.

SLOGAN: Unlocking the power of meaningful connections
LOGO/TITLE: Should be the name as shown in image with only the name "KelvoLink" on it
COLORS: Purplish/blue hues. Should not be too feminine
NOTE: The user should only click once when signing up/entering their email.

Product: A recruiting platform that matches employers/employees with A.I. and prioritizing cultural fit/values system before skills. The industry we are tackling first is the caregiving industry (nannies, tutors, elderly). All users will be background screened and that info lives on the blockchain. All users will have the option to review and be reviewed/rated.

```html
<!DOCTYPE html>
<html lang="en">
<head>
<meta charset="utf-8">
<title>KelvoLink — Coming Soon</title>
<link rel="stylesheet" href="https://fonts.googleapis.com/css2?family=Montserrat:wght@300;500;600&family=Roboto:wght@400&display=swap">
<style>
  :root {
    --night: #0c0a1f;
    --violet-deep: #1c1040;
    --violet-glow: #3a1d72;
    --teal-glow: #2f7f95;
    --blue-glow: #3a6fb3;
    --white: #ffffff;
    --placeholder-grey: #7a7a7a;
    --button-purple: #4b2497;
    --screen-teal: #4fb6cc;
    --screen-teal-dark: #1f8fae;
    --frame-dark: #15202b;
  }
  * { box-sizing: border-box; margin: 0; padding: 0; }
  html, body { width: 1200px; height: 667px; overflow: hidden; }
  body { background: var(--night); }

  .coming-soon {
    position: relative;
    width: 1200px;
    height: 667px;
    overflow: hidden;
    background:
      radial-gradient(ellipse 420px 300px at 1180px 60px, var(--violet-glow), transparent 70%),
      radial-gradient(ellipse 520px 260px at 1000px 700px, var(--blue-glow), transparent 70%),
      radial-gradient(ellipse 380px 420px at 60px 400px, var(--teal-glow), transparent 70%),
      radial-gradient(ellipse 700px 500px at 700px 200px, var(--violet-deep), transparent 75%),
      var(--night);
  }

  .phone-mockup {
    position: absolute;
    left: 99px;
    top: 81px;
    width: 338px;
    height: 553px;
    border-radius: 46px;
    border: 8px solid var(--frame-dark);
    background: linear-gradient(170deg, var(--screen-teal) 0%, var(--screen-teal-dark) 100%);
    transform: rotate(-3deg);
    box-shadow: 0 20px 40px rgba(0,0,0,0.45);
  }

  .hero-copy {
    position: absolute;
    left: 491px;
    top: 150px;
  }

  .brand-name {
    font-family: "Montserrat", sans-serif;
    font-weight: 300;
    font-size: 70px;
    line-height: 60px;
    letter-spacing: 10px;
    color: var(--white);
    text-transform: uppercase;
  }

  .slogan {
    margin-top: 54px;
    font-family: "Roboto", sans-serif;
    font-weight: 400;
    font-size: 26px;
    color: var(--white);
  }

  .signup-form {
    margin-top: 36px;
    display: flex;
    flex-direction: column;
    gap: 38px;
  }

  .email-field {
    width: 316px;
    height: 65px;
    border: none;
    border-radius: 33px;
    background: var(--white);
    padding-left: 29px;
    font-family: "Montserrat", sans-serif;
    font-weight: 500;
    font-size: 17px;
    color: var(--night);
  }
  .email-field::placeholder { color: var(--placeholder-grey); }

  .signup-button {
    width: 188px;
    height: 64px;
    border: none;
    border-radius: 32px;
    background: var(--button-purple);
    color: var(--white);
    font-family: "Montserrat", sans-serif;
    font-weight: 600;
    font-size: 19px;
    letter-spacing: 0.5px;
  }
</style>
</head>
<body>
  <main class="coming-soon">
    <div class="phone-mockup" role="img" aria-label="Smartphone showing the KelvoLink coming-soon screen with an email field and a Notify Me button"></div>

    <section class="hero-copy">
      <h1 class="brand-name">KelvoLink</h1>
      <p class="slogan">Unlocking the Power Of Meaningful Connections</p>
      <form class="signup-form" action="#" method="post">
        <input class="email-field" type="email" name="email" placeholder="ENTER EMAIL" aria-label="Email address">
        <button class="signup-button" type="submit">SIGN ME UP</button>
      </form>
    </section>
  </main>
</body>
</html>
```